BrimFalcon Business Cards

We have a defined brand. Please visit our website to get a feel for the product and the color pallets. www.brimfalcon-example.com

We need an updated, world class business card design. (See the attached existing card design). Please utilize BOTH sides of the card as shown and be creative with the layout. I do want the horse head icon to be positioned as it is with the existing card.

The remainder of the layout can be customized and I also want it vertically oriented.

Attached are the logo files and please use the colors as follows:
Green - #A5CE39
Tan - #CDBD99
Black

Feel free to play with the colors.

```html
<!DOCTYPE html>
<html lang="en">
<head>
<meta charset="utf-8">
<title>BrimFalcon Labs – Business Card</title>
<link rel="stylesheet" href="https://fonts.googleapis.com/css2?family=Open+Sans:wght@400;600;700&display=swap">
<style>
  :root {
    --green: #A5CE39;
    --black: #0b0b0b;
    --white: #ffffff;
    --backdrop: #e4e1da;
  }
  * { box-sizing: border-box; margin: 0; padding: 0; }
  html, body {
    width: 1200px; height: 900px; overflow: hidden;
    background: var(--backdrop);
    font-family: "Open Sans", Arial, sans-serif;
  }
  .card {
    position: absolute; top: 120px;
    width: 390px; height: 660px;
    background: var(--white);
    border: 6px solid var(--green);
    border-radius: 24px;
    box-shadow: 0 10px 24px rgba(0,0,0,.18);
  }
  .card--front { left: 150px; padding: 34px 28px; }
  .card--back  { left: 660px; }

  /* front */
  .brand { display: flex; align-items: center; gap: 12px; margin-bottom: 32px; }
  .brand__dot { width: 40px; height: 40px; border-radius: 50%; background: var(--black); flex: none; }
  .brand__name { font-weight: 700; font-size: 30px; color: var(--black); line-height: 1; }
  .brand__tagline { font-size: 12px; letter-spacing: 3px; color: var(--black); margin-top: 6px; }

  .info-list { list-style: none; display: flex; flex-direction: column; gap: 30px; }
  .info-bar {
    display: flex; align-items: center; gap: 14px;
    height: 66px; padding: 0 20px;
    background: var(--black);
    border: 3px solid var(--green);
    border-radius: 16px;
    color: var(--green);
    font-size: 17px;
    white-space: nowrap;
  }
  .info-bar--name { height: 82px; flex-direction: column; justify-content: center; align-items: center; gap: 2px; }
  .person__name { font-weight: 700; font-size: 24px; }
  .person__role { font-size: 17px; }
  .info-bar svg { width: 24px; height: 24px; flex: none; }
  .info-bar--small { font-size: 15px; }
  .info-bar--address { line-height: 1.25; }

  /* back */
  .back__mark {
    position: absolute; left: 0; right: 0; top: 220px;
    display: flex; flex-direction: column; align-items: center; gap: 18px;
  }
  .back__dot { width: 26px; height: 26px; border-radius: 50%; background: var(--green); }
  .back__name { font-weight: 700; font-size: 46px; color: var(--black); }
  .back__site {
    position: absolute; left: 0; right: 0; bottom: 40px;
    text-align: center; font-size: 20px; color: var(--green);
  }
  .back__site span { color: var(--black); }
</style>
</head>
<body>

<section class="card card--front" aria-label="Card front">
  <header class="brand">
    <div class="brand__dot"></div>
    <div>
      <div class="brand__name">BrimFalcon Labs</div>
      <div class="brand__tagline">Electric Motion Studio</div>
    </div>
  </header>

  <ul class="info-list">
    <li class="info-bar info-bar--name">
      <span class="person__name">Dana Merrow</span>
      <span class="person__role">President &amp; CEO</span>
    </li>
    <li class="info-bar">
      <svg viewBox="0 0 24 24" fill="var(--green)"><path d="M6.6 10.8a15 15 0 0 0 6.6 6.6l2.2-2.2c.3-.3.7-.4 1-.2 1.1.4 2.3.6 3.6.6.6 0 1 .4 1 1V20c0 .6-.4 1-1 1A17 17 0 0 1 3 4c0-.6.4-1 1-1h3.5c.6 0 1 .4 1 1 0 1.3.2 2.5.6 3.6.1.3 0 .7-.2 1z"/></svg>
      555.014.7391
    </li>
    <li class="info-bar info-bar--small">
      <svg viewBox="0 0 24 24" fill="none" stroke="var(--green)" stroke-width="2"><rect x="3" y="5" width="18" height="14" rx="1"/><path d="M3 6l9 7 9-7"/></svg>
      dana@brimfalcon-example.com
    </li>
    <li class="info-bar info-bar--small">
      <svg viewBox="0 0 24 24" fill="none" stroke="var(--green)" stroke-width="2"><circle cx="12" cy="12" r="9"/><path d="M3 12h18M12 3c3 3 3 15 0 18M12 3c-3 3-3 15 0 18"/></svg>
      www.brimfalcon-example.com
    </li>
    <li class="info-bar info-bar--address">
      <svg viewBox="0 0 24 24" fill="var(--green)"><path d="M12 2a7 7 0 0 0-7 7c0 5 7 13 7 13s7-8 7-13a7 7 0 0 0-7-7zm0 9.5A2.5 2.5 0 1 1 12 6.5a2.5 2.5 0 0 1 0 5z"/></svg>
      <span>Harrow Bay, Westland<br>canada</span>
    </li>
  </ul>
</section>

<section class="card card--back" aria-label="Card back">
  <div class="back__mark">
    <div class="back__dot"></div>
    <div class="back__name">BrimFalcon</div>
  </div>
  <p class="back__site"><span>www.</span>brimfalcon-example.com</p>
</section>

</body>
</html>
```